Business Card Design Project : Ridgeline Press

In preparation for market launch, Tamarind's Ridgeline Press require the development of a business card. Ridgeline Press is a Community online publishing web portal. We provide the the city of Whistler located in B.C. (Canada) business directories, News, Classified ads, News, Events and blogs etc.

The main focus of the brand is to help local businesses to corporate with their online advertisement and marketing. Meeting our clients face to face is a must (B2B).

Target Market(s)

The target market is B2B customers. Business Owners to Marketing, advertising Managers

Industry/Entity Type

Business

Requirements
Must have
• - The business card will be two sided.
the BACK side will have our logo which consist of (icon, url,slogan) submited. The logo will be middle and centred.

The FRONT side should have company details:

Company Legal Name: TAMARIND RIDGELINE MEDIA

Owen Farsk
Director of Sales & Marketing

www.tamarindridgeline.biz
owen@tamarindridgeline.biz

Phone: 604 317 8842
#2714 - 582 E. Halvern St.
Vancouver, B.C. V7K2R4 Canada
Nice to have
• - For the "FRONT" side of our business card. You can separate or re-arrange with our logo components (icon, logo,slogan). It does not have to be together.

Also our company legal name is rather long so arrange or organize the name in a way to make it shorter. Your experience and creativity will have to come in play.
Should not have
• should not have other colors beside logo color and black text (2 colors). Also nothing Three dimensional

```html
<!DOCTYPE html>
<html lang="en">
<head>
<meta charset="utf-8">
<title>Tamarind Ridgeline Media – Business Card</title>
<link rel="stylesheet" href="https://fonts.googleapis.com/css2?family=Open+Sans:wght@400;600;700;800&display=swap">
<style>
  :root {
    --brand-blue: #2a7fc4;
    --ink: #111214;
    --paper: #ffffff;
    --stage: #ecebe8;
    --shadow: rgba(0, 0, 0, 0.18);
  }
  * { box-sizing: border-box; margin: 0; padding: 0; }
  html, body {
    width: 1200px; height: 900px; overflow: hidden;
    background: var(--stage);
    font-family: "Open Sans", Arial, sans-serif;
  }
  .stage {
    width: 1200px; height: 900px;
    display: flex; align-items: center; justify-content: center; gap: 40px;
  }
  .card {
    position: relative;
    width: 540px; height: 309px;
    background: var(--paper);
    box-shadow: 0 6px 18px var(--shadow);
    overflow: hidden;
  }

  /* Wordmark lockup */
  .lockup { display: flex; align-items: center; gap: 12px; }
  .lockup-mark { width: 30px; height: 30px; background: var(--brand-blue); flex: none; }
  .lockup-name {
    font-weight: 800; color: var(--ink); letter-spacing: -0.2px; line-height: 1;
    text-transform: uppercase;
  }
  .lockup-slogan { color: var(--brand-blue); font-weight: 400; margin-top: 4px; line-height: 1; }

  /* Back side */
  .card-back .lockup {
    position: absolute; left: 50%; top: 46%;
    transform: translate(-50%, -50%);
  }
  .card-back .lockup-name { font-size: 22px; }
  .card-back .lockup-slogan { font-size: 16px; }
  .url-tab {
    position: absolute; right: 0;
    background: var(--brand-blue); color: var(--paper);
    font-size: 11.5px; font-weight: 600;
    display: flex; align-items: center; justify-content: flex-end;
    padding-right: 16px;
    clip-path: polygon(18px 0, 100% 0, 100% 100%, 0 100%);
  }
  .card-back .url-tab { bottom: 0; width: 190px; height: 36px; }

  /* Front side */
  .card-front .lockup { position: absolute; left: 200px; top: 50px; gap: 10px; }
  .card-front .lockup-mark { width: 24px; height: 24px; }
  .card-front .lockup-name { font-size: 17px; }
  .card-front .lockup-slogan { font-size: 13px; }

  .person { position: absolute; left: 34px; top: 148px; }
  .person-name { font-size: 18px; font-weight: 800; color: var(--ink); text-transform: uppercase; line-height: 1.1; }
  .person-title { font-size: 12.5px; font-weight: 600; color: var(--brand-blue); margin-top: 2px; }

  .contact-accent {
    position: absolute; left: 24px; bottom: 0; width: 110px; height: 100px;
    background: var(--brand-blue);
    clip-path: polygon(0 100%, 22px 0, 36px 0, 14px 100%);
  }
  .contact-band {
    position: absolute; left: 40px; right: 0; bottom: 0; height: 100px;
    background: var(--ink);
    clip-path: polygon(22px 0, 100% 0, 100% 100%, 0 100%);
  }
  .card-front .url-tab { top: 209px; width: 170px; height: 32px; }

  .contact-list {
    position: absolute; left: 72px; bottom: 12px;
    list-style: none; color: var(--paper); font-size: 12px; line-height: 1.55;
  }
  .contact-list li { display: flex; align-items: center; gap: 10px; }
  .contact-icon { width: 11px; height: 11px; fill: var(--brand-blue); flex: none; }
</style>
</head>
<body>
<main class="stage">

  <section class="card card-back" aria-label="Card back">
    <div class="lockup">
      <span class="lockup-mark"></span>
      <div>
        <div class="lockup-name">Tamarind Ridgeline Media</div>
        <div class="lockup-slogan">Your information gateway</div>
      </div>
    </div>
    <div class="url-tab">www.tamarindridgeline.biz</div>
  </section>

  <section class="card card-front" aria-label="Card front">
    <div class="lockup">
      <span class="lockup-mark"></span>
      <div>
        <div class="lockup-name">Tamarind Ridgeline Media</div>
        <div class="lockup-slogan">Your information gateway</div>
      </div>
    </div>

    <div class="person">
      <div class="person-name">Owen Farsk</div>
      <div class="person-title">Director of Sales &amp; Marketing</div>
    </div>

    <div class="contact-accent"></div>
    <div class="contact-band"></div>
    <div class="url-tab">www.tamarindridgeline.biz</div>

    <ul class="contact-list">
      <li>
        <svg class="contact-icon" viewBox="0 0 12 12" aria-hidden="true"><path d="M6 1 L11.5 6 H10 V11 H7.2 V8 H4.8 V11 H2 V6 H0.5 Z"/></svg>
        #2714 - 582 E. Halvern St. Vancouver, B.C V7K2R4 Canada
      </li>
      <li>
        <svg class="contact-icon" viewBox="0 0 12 12" aria-hidden="true"><path d="M2.2 0.8 L4.3 0.8 L5.2 3.4 L3.9 4.4 C4.6 5.9 6.1 7.4 7.6 8.1 L8.6 6.8 L11.2 7.7 L11.2 9.8 C11.2 10.6 10.6 11.2 9.8 11.2 C5 10.9 1.1 7 0.8 2.2 C0.8 1.4 1.4 0.8 2.2 0.8 Z"/></svg>
        604 317 8842
      </li>
      <li>
        <svg class="contact-icon" viewBox="0 0 12 12" aria-hidden="true"><path d="M0.5 2 H11.5 V10 H0.5 Z M1.4 2.9 L6 6.6 L10.6 2.9 Z" fill-rule="evenodd"/></svg>
        owen@tamarindridgeline.biz
      </li>
    </ul>
  </section>

</main>
</body>
</html>
```